Food broker, trader, wholesaler, liquidator looking for a 5 pages website

Looking for a 5 pages website design. We are food brokers, traders, wholesaler and closeout buyer working with manufacturers, distributors, importers sell to retailers, food service operators and industrial (ingredients). We help market their products. We are a resource for those who need a solution in the distribution/selling/placement of food on the shelves, kitchens and pantries. Whether we open new accounts with new products or sell short dated inventory, we know where to go and get results.

Target Market(s)

Food manufacturers, food distributors, food brokers

Coding

Coded - Design and coding required

Number of Pages Required

4 page

Font styles to use
Serif

Requirements
Must have
• Food-food production-warehouse-Food packaging-people meeting-trucks-supermarket shelves-

```html
<!DOCTYPE html>
<html lang="en">
<head>
<meta charset="utf-8">
<title>Keelhaven Foods</title>
<link href="https://fonts.googleapis.com/css2?family=Noticia+Text:wght@400;700&family=Montserrat:wght@400;500&display=swap" rel="stylesheet">
<style>
:root{
  --navy:#0b0b55;
  --ink:#333;
  --muted:#666;
  --white:#fff;
  --line:#d8d8d8;
  --footer:#222;
  --serif:'Noticia Text', Georgia, serif;
  --sans:'Montserrat', Arial, sans-serif;
}
*{margin:0;padding:0;box-sizing:border-box}
html,body{width:1200px;height:3617px;overflow:hidden;background:var(--white);font-family:var(--serif);color:var(--ink)}
.page{position:relative;width:1200px;height:3617px;overflow:hidden}

/* header */
.site-header{position:absolute;top:0;left:0;width:1200px;height:108px;background:var(--white);z-index:3}
.brand-badge{position:absolute;left:110px;top:-24px;width:202px;height:202px;border-radius:50%;background:var(--white);z-index:4;display:flex;align-items:flex-end;justify-content:center;padding-bottom:76px}
.brand-badge span{font-family:var(--serif);font-weight:700;font-size:14px;color:var(--navy);letter-spacing:.3px;text-transform:uppercase}
.nav{position:absolute;top:46px;left:0;width:1200px;font-size:14px;color:#222}
.nav a{position:absolute;transform:translateX(-50%);white-space:nowrap;color:#222;text-decoration:none}
.nav a.active{color:var(--navy);font-weight:700}

/* hero */
.hero{position:absolute;top:108px;left:0;width:1200px;height:706px;
  background:linear-gradient(90deg,#8a6a44 0%,#c9a57a 20%,#e4d3bd 45%,#eadbc6 55%,#c59d72 80%,#7b5d3d 100%);
  clip-path:path('M0 0 H1200 V580 Q600 880 0 580 Z')}
.hero-panel{position:absolute;left:271px;top:243px;width:658px;height:268px;background:rgba(255,255,255,.12)}
.hero-title{position:absolute;top:266px;width:1200px;text-align:center;font-size:48px;color:var(--white);font-weight:400}
.hero-text{position:absolute;top:338px;left:250px;width:700px;text-align:center;font-size:18px;line-height:36px;color:var(--white)}
.btn-navy{position:absolute;background:var(--navy);color:var(--white);font-size:15px;display:flex;align-items:center;justify-content:center;border-radius:3px}

/* headings */
.section-title{position:absolute;width:1200px;text-align:center;font-size:42px;color:var(--navy);font-weight:400}
.section-sub{position:absolute;width:1200px;text-align:center;font-size:16px;color:#444}

.process{position:absolute;left:0;top:960px}
.process text{font-family:var(--serif);font-size:20px;fill:#222}
.stage-icon{fill:none;stroke:var(--navy);stroke-width:2;stroke-linecap:round;stroke-linejoin:round}

/* about */
.about{position:absolute;top:1664px;left:0;width:1200px;height:483px;background:var(--navy);overflow:hidden}
.about-photo{position:absolute;left:685px;top:0;width:515px;height:483px;background:linear-gradient(135deg,#c8ccd4 0%,#8e9aab 40%,#a99f86 70%,#5d6470 100%);clip-path:ellipse(560px 420px at 560px 241px)}
.about-title{position:absolute;left:139px;top:70px;font-size:46px;color:var(--white);font-weight:400}
.about-rule{position:absolute;left:139px;top:136px;width:60px;height:3px;background:var(--white)}
.about-text{position:absolute;left:139px;top:168px;width:468px;font-size:12.5px;line-height:30px;color:var(--white);text-align:justify}
.btn-outline{position:absolute;left:139px;top:375px;width:131px;height:48px;border:1px solid var(--white);border-radius:2px;color:var(--white);font-size:14px;display:flex;align-items:center;justify-content:center}

/* services */
.service-card{position:absolute;top:2310px;width:309px;height:392px;background:var(--white);border:1px solid #e6e6e6;box-shadow:0 0 6px rgba(0,0,0,.08)}
.service-photo{position:absolute;left:10px;top:10px;width:289px;height:214px}
.service-title{position:absolute;top:252px;width:100%;text-align:center;font-size:20px;color:#222;font-weight:400}
.service-rule{position:absolute;top:290px;left:134px;width:42px;height:2px;background:var(--navy)}
.service-text{position:absolute;top:306px;left:20px;width:269px;text-align:center;font-family:var(--sans);font-size:12.5px;line-height:24px;color:var(--muted)}

/* contact */
.contact{position:absolute;top:2762px;left:0;width:1200px;height:480px;background:linear-gradient(180deg,#efefef,#f3f2f1 60%,#ece9e6)}
.field{position:absolute;background:var(--white);border:1px solid #cfcfcf;font-size:13px;color:#555;padding:13px 16px}

/* footer */
.footer{position:absolute;top:3242px;left:0;width:1200px;height:375px;background:var(--footer);color:var(--white)}
.footer-badge{position:absolute;left:169px;top:56px;width:140px;height:140px;border-radius:50%;background:var(--white)}
.footer-name{position:absolute;left:100px;top:206px;width:280px;text-align:center;font-weight:700;font-size:19px;text-transform:uppercase;letter-spacing:.3px}
.footer-heading{position:absolute;top:44px;font-size:24px;font-weight:400}
.footer-list{position:absolute;top:96px;list-style:none;font-family:var(--sans);font-size:14px}
.footer-list li{height:35px;padding-left:27px;position:relative}
.footer-list li::before{content:'»';position:absolute;left:2px;top:-2px}
.footer-note{position:absolute;left:836px;top:100px;width:260px;font-family:var(--sans);font-size:14px;line-height:24px}
.footer-input{position:absolute;left:836px;top:168px;width:250px;height:43px;background:var(--white);color:#444;font-family:var(--sans);font-size:14px;padding:13px 14px}
.footer-submit{position:absolute;left:836px;top:216px;width:96px;height:40px;background:var(--navy);font-family:var(--sans);font-size:14px;display:flex;align-items:center;justify-content:center}
.footer-rule{position:absolute;left:112px;top:298px;width:976px;height:1px;background:#444}
.copyright{position:absolute;top:326px;width:1200px;text-align:center;font-family:var(--sans);font-size:14px}
</style>
</head>
<body>
<div class="page">

  <header class="site-header">
    <nav class="nav">
      <a class="active" style="left:605px">Home</a>
      <a style="left:702px">About Us</a>
      <a style="left:821px">What we do</a>
      <a style="left:933px">Contact</a>
      <a style="left:1047px">Giving Back</a>
    </nav>
  </header>
  <div class="brand-badge"><span>Keelhaven Foods</span></div>

  <section class="hero" role="img" aria-label="Supermarket aisle with stocked shelves, softly blurred">
    <div class="hero-panel"></div>
    <h1 class="hero-title">Keelhaven Foods</h1>
    <p class="hero-text">Sed ut perspiciatis unde omnis iste natus error sit voluptatem accusantium doloremque laudantium, totam rem aperiam</p>
    <div class="btn-navy" style="left:533px;top:425px;width:132px;height:48px">Read More</div>
  </section>

  <h2 class="section-title" style="top:842px">Our Process</h2>
  <p class="section-sub" style="top:914px">Sed ut perspiciatis unde omnis iste natus error sit voluptatem accusantium doloremque</p>

  <svg class="process" width="1200" height="680" viewBox="0 960 1200 680">
    <defs>
      <marker id="arrowhead" markerWidth="12" markerHeight="12" refX="9" refY="6" orient="auto" markerUnits="userSpaceOnUse">
        <path d="M0 0 L10 6 L0 12" fill="none" stroke="#0b0b55" stroke-width="2"/>
      </marker>
    </defs>
    <g fill="none" stroke="#0b0b55" stroke-width="3" marker-end="url(#arrowhead)">
      <path d="M622 1045 Q680 1050 722 1072"/>
      <path d="M820 1158 Q850 1200 862 1252"/>
      <path d="M860 1382 Q845 1440 812 1480"/>
      <path d="M708 1560 Q650 1585 565 1584"/>
      <path d="M447 1535 Q405 1510 378 1468"/>
      <path d="M332 1350 Q328 1290 340 1235"/>
      <path d="M405 1124 Q440 1085 496 1062"/>
    </g>
    <g fill="#fff" stroke="#0b0b55" stroke-width="2">
      <circle cx="557" cy="1050" r="54"/>
      <circle cx="770" cy="1114" r="54"/>
      <circle cx="858" cy="1315" r="54"/>
      <circle cx="762" cy="1523" r="54"/>
      <circle cx="505" cy="1565" r="54"/>
      <circle cx="344" cy="1416" r="54"/>
      <circle cx="363" cy="1176" r="54"/>
    </g>

    <!-- food production: machine -->
    <g class="stage-icon" transform="translate(557,1050)" role="img" aria-label="Food production machine icon">
      <rect x="-20" y="-22" width="40" height="30" rx="2"/>
      <circle cx="5" cy="-7" r="8"/>
      <circle cx="5" cy="-7" r="3"/>
      <rect x="-15" y="-17" width="8" height="6"/>
      <line x1="-15" y1="-3" x2="-8" y2="-3"/>
      <line x1="0" y1="8" x2="0" y2="20"/>
      <line x1="-10" y1="20" x2="10" y2="20"/>
      <line x1="-6" y1="14" x2="6" y2="14"/>
    </g>

    <!-- warehouse -->
    <g class="stage-icon" transform="translate(770,1114)" role="img" aria-label="Warehouse icon">
      <path d="M-24 -6 L0 -20 L24 -6 V22 H-24 Z"/>
      <rect x="-13" y="2" width="26" height="20"/>
      <line x1="-13" y1="9" x2="13" y2="9"/>
      <line x1="-13" y1="15" x2="13" y2="15"/>
      <rect x="-9" y="15" width="6" height="7"/>
      <rect x="3" y="15" width="6" height="7"/>
    </g>

    <!-- food packaging: jar with fish -->
    <g class="stage-icon" transform="translate(858,1315)" role="img" aria-label="Food packaging icon">
      <rect x="-13" y="-24" width="26" height="8" rx="2"/>
      <path d="M-17 -16 H17 V22 H-17 Z"/>
      <line x1="-17" y1="-6" x2="17" y2="-6"/>
      <line x1="-17" y1="16" x2="17" y2="16"/>
      <ellipse cx="-2" cy="5" rx="8" ry="5"/>
      <path d="M6 5 L13 0 V10 Z"/>
    </g>

    <!-- people meeting -->
    <g class="stage-icon" transform="translate(762,1523)" role="img" aria-label="People meeting icon">
      <circle cx="0" cy="-14" r="6"/>
      <circle cx="-14" cy="-7" r="5"/>
      <circle cx="14" cy="-7" r="5"/>
      <path d="M-9 20 V2 Q0 -6 9 2 V20"/>
      <path d="M-23 20 V6 Q-16 0 -10 4"/>
      <path d="M23 20 V6 Q16 0 10 4"/>
      <line x1="-4" y1="8" x2="-4" y2="20"/>
      <line x1="4" y1="8" x2="4" y2="20"/>
    </g>

    <!-- truck -->
    <g class="stage-icon" transform="translate(505,1565)" role="img" aria-label="Delivery truck icon">
      <rect x="-24" y="-16" width="28" height="26"/>
      <path d="M4 -8 H15 L23 2 V10 H4 Z"/>
      <path d="M8 -4 H14 L18 2 H8 Z"/>
      <circle cx="-13" cy="14" r="4"/>
      <circle cx="14" cy="14" r="4"/>
      <line x1="-18" y1="-8" x2="-4" y2="-8"/>
    </g>

    <!-- supermarket shelves -->
    <g class="stage-icon" transform="translate(344,1416)" role="img" aria-label="Supermarket shelves icon">
      <rect x="-22" y="-20" width="44" height="42"/>
      <line x1="-22" y1="-6" x2="22" y2="-6"/>
      <line x1="-22" y1="8" x2="22" y2="8"/>
      <rect x="-17" y="-16" width="6" height="10"/>
      <rect x="-8" y="-14" width="7" height="8"/>
      <rect x="3" y="-17" width="5" height="11"/>
      <rect x="11" y="-13" width="7" height="7"/>
      <rect x="-17" y="0" width="9" height="8"/>
      <rect x="-5" y="-2" width="6" height="10"/>
      <rect x="5" y="1" width="12" height="7"/>
      <rect x="-15" y="13" width="8" height="9"/>
      <rect x="-3" y="14" width="8" height="8"/>
      <rect x="9" y="12" width="8" height="10"/>
    </g>

    <!-- food bowl -->
    <g class="stage-icon" transform="translate(363,1176)" role="img" aria-label="Food bowl icon">
      <path d="M-24 2 H24 Q22 18 0 20 Q-22 18 -24 2 Z"/>
      <path d="M-14 2 Q0 -14 14 2"/>
      <path d="M-8 2 Q0 -8 8 2"/>
      <line x1="-12" y1="24" x2="12" y2="24"/>
      <path d="M-6 -14 Q-9 -19 -6 -24"/>
      <path d="M0 -16 Q-3 -21 0 -26"/>
      <path d="M6 -14 Q3 -19 6 -24"/>
    </g>

    <text x="596" y="1305" text-anchor="middle" style="font-size:26px;font-weight:700;fill:#0b0b55">Keelhaven Foods</text>
    <text x="394" y="1002">Food</text><text x="394" y="1036">Production</text>
    <text x="842" y="1117">Warehouse</text>
    <text x="928" y="1309">Food</text><text x="928" y="1342">Packaging</text>
    <text x="834" y="1521">People</text><text x="834" y="1555">Meeting</text>
    <text x="378" y="1587">Trucks</text>
    <text x="153" y="1416">Supermarket</text><text x="153" y="1450">Shelves</text>
    <text x="246" y="1178">Food</text>
  </svg>

  <section class="about">
    <div class="about-photo" role="img" aria-label="Smiling warehouse worker holding a clipboard between stocked racks"></div>
    <h2 class="about-title">About Us</h2>
    <div class="about-rule"></div>
    <p class="about-text">Keelhaven Foods works with food manufacturers, brand owners, distributors and wholesalers market their products. Retail, Food Service and Industrial ingredients. Founded in 2008, Keelhaven Foods started with the distribution of gluten free products understanding the need to provide access to unique flavors and products for the celiac consumers. From this, we expanded into deli, dairy, groceries, frozen and beverages.</p>
    <div class="btn-outline">READ MORE</div>
  </section>

  <h2 class="section-title" style="top:2188px">What We Do</h2>
  <p class="section-sub" style="top:2251px">Sed ut perspiciatis unde omnis iste natus error sit voluptatem accusantium doloremque</p>

  <article class="service-card" style="left:112px">
    <div class="service-photo" role="img" aria-label="Team meeting in a boardroom with a sales chart on screen" style="background:linear-gradient(135deg,#2a3140,#6e7a8c 55%,#c9cfd6)"></div>
    <h3 class="service-title">Sales &amp; Marketing</h3>
    <div class="service-rule"></div>
    <p class="service-text">we connect food buyers and sellers through a dedicated approach.</p>
  </article>
  <article class="service-card" style="left:445px">
    <div class="service-photo" role="img" aria-label="Hands typing on a laptop in front of trading screens" style="background:linear-gradient(135deg,#26303d,#5a6878 50%,#c9a77c)"></div>
    <h3 class="service-title">Trading</h3>
    <div class="service-rule"></div>
    <p class="service-text">we purchase goods anywhere and ship them Nationwide and Export.</p>
  </article>
  <article class="service-card" style="left:779px">
    <div class="service-photo" role="img" aria-label="Two warehouse staff checking a cardboard box against a tablet" style="background:linear-gradient(135deg,#7d6a55,#9fb1c6 50%,#c7a57f)"></div>
    <h3 class="service-title">Closeout/Excess Inventory</h3>
    <div class="service-rule"></div>
    <p class="service-text">we buy closeouts and excess inventory for prisons, outlet stores and discounters.</p>
  </article>

  <section class="contact" role="img" aria-label="Faded warehouse interior behind the contact form">
    <h2 class="section-title" style="top:50px">Contact Us</h2>
    <p class="section-sub" style="top:108px">Sed ut perspiciatis unde omnis iste natus error sit voluptatem accusantium</p>
    <div class="field" style="left:281px;top:161px;width:314px;height:44px">First Name :</div>
    <div class="field" style="left:606px;top:161px;width:313px;height:44px">Last Name :</div>
    <div class="field" style="left:281px;top:218px;width:314px;height:43px">Email :</div>
    <div class="field" style="left:606px;top:218px;width:313px;height:43px">Phone :</div>
    <div class="field" style="left:281px;top:272px;width:638px;height:87px">Message :</div>
    <div class="btn-navy" style="left:526px;top:382px;width:148px;height:47px;border-radius:0;font-size:14px">SUBMIT</div>
  </section>

  <footer class="footer">
    <div class="footer-badge"></div>
    <div class="footer-name">Keelhaven Foods</div>

    <h4 class="footer-heading" style="left:396px">Quick Links</h4>
    <ul class="footer-list" style="left:396px">
      <li>Home</li><li>About Us</li><li>What we do</li><li>Contact</li><li>Giving Back</li>
    </ul>

    <h4 class="footer-heading" style="left:613px">Services</h4>
    <ul class="footer-list" style="left:613px">
      <li>Sed ut perspiciatis</li><li>unde omnis iste</li><li>natus error sit</li><li>voluptatem</li><li>accusantium</li>
    </ul>

    <h4 class="footer-heading" style="left:836px">Newsletter</h4>
    <p class="footer-note">Sed ut perspiciatis unde omnis iste natus error sit voluptatem</p>
    <div class="footer-input">Email :</div>
    <div class="footer-submit">SUBMIT</div>

    <div class="footer-rule"></div>
    <p class="copyright">© Copyright 2020 Keelhaven Foods.All Rights Reserved</p>
  </footer>

</div>
</body>
</html>
```